Motor Oil Lubricant Package Labels

We are looking for a logo and label that we can put on our motor oil bottle 1 liter and 5 liter. The name of our motor oil is Corvana. We want to design our flagship logo for CORVANA MOTOR OILS and as well as the label that will go on the bottle. We have some drafts that we have come up with attached and would like to see more options. The concept of a timeless motor oil and the endless loop of lubricating oils incorporated in the design. We will have full synthetic motor oil, a synthetic blend motor, ATF III transmission fluid, KRL-VI transmission fluid. hydraulic oils etc. Examples will be attached
Target Market(s)
Automotive Lubricants and Chemicals
Industry/Entity Type
Automotive
Logo Text
Corvana Lubricants
Font styles to use
Other font styles liked:
- Let designer choose
Requirements
Must have
- The Corvana sign incorporated in a very cool way to our name. Our brand needs to stick out
Nice to have
- Automotive lubricant related and colors red, white, and blue incorporated in the design
Should not have
- Images of individuals and or topics not related to automotive lubricants.

```html
<!DOCTYPE html>
<html lang="en">
<head>
<meta charset="utf-8">
<title>Corvana Synthetic Blend 5W-30 Labels</title>
<link rel="stylesheet" href="https://fonts.googleapis.com/css2?family=Roboto+Condensed:wght@300;400;700;900&family=Russo+One&display=swap">
<style>
  :root {
    --brand-blue: #2c55a8;
    --brand-red: #ec1c24;
    --ink: #222222;
    --silver-light: #eceded;
    --silver-mid: #c9cacc;
    --silver-dark: #a9abae;
    --gold-light: #f3d37a;
    --gold-dark: #b7801f;
    --white: #ffffff;
  }
  * { box-sizing: border-box; margin: 0; padding: 0; }
  html, body { width: 1200px; height: 850px; overflow: hidden; background: var(--white); }
  body { position: relative; font-family: "Roboto Condensed", sans-serif; color: var(--ink); }

  .label {
    position: absolute; top: 48px; width: 469px; height: 759px;
    border-radius: 26px; overflow: hidden;
    background: linear-gradient(100deg, var(--silver-dark) 0%, var(--silver-light) 35%, var(--silver-mid) 60%, var(--silver-light) 80%, var(--silver-dark) 100%);
  }
  .label--front { left: 104px; }
  .label--back { left: 627px; }
  .label__shapes { position: absolute; inset: 0; width: 100%; height: 100%; }

  .abs { position: absolute; white-space: nowrap; }

  .brand-name { color: var(--brand-blue); font-weight: 900; line-height: 1; letter-spacing: 1px; }
  .brand-sub { color: var(--ink); font-weight: 900; line-height: 1; letter-spacing: 1px; }

  .outlined {
    font-family: "Russo One", sans-serif; color: var(--white); line-height: 1;
    -webkit-text-stroke: 3px #111; paint-order: stroke fill;
  }

  .tagline { font-family: "Russo One", sans-serif; text-align: center; line-height: 1; }
  .tagline__top { display: block; color: var(--brand-blue); }
  .tagline__bottom {
    display: inline-block; color: var(--white); background: var(--brand-red);
    padding: 2px 8px; margin-top: 5px;
  }

  .seal {
    position: absolute; border-radius: 50%;
    background: radial-gradient(circle at 40% 35%, var(--gold-light), var(--gold-dark) 75%);
  }
  .seal::after { content: ""; position: absolute; inset: 22%; border-radius: 50%; background: var(--white); }

  /* Front */
  .front-name { left: 35px; top: 134px; font-size: 72px; }
  .front-sub { left: 203px; top: 206px; font-size: 18px; }
  .front-grade-title { left: 50px; top: 264px; width: 248px; text-align: center; font-size: 21px; }
  .front-tagline { left: 66px; top: 302px; width: 220px; font-size: 18px; }
  .promise {
    left: 80px; top: 357px; width: 200px; text-align: center; white-space: normal;
    font-family: "Russo One", sans-serif; font-size: 11px; line-height: 1.45; color: #333; letter-spacing: .5px;
  }
  .front-seal { left: 28px; top: 500px; width: 100px; height: 100px; }
  .volume { left: 35px; top: 704px; font-size: 26px; font-weight: 700; }
  .origin { left: 222px; top: 708px; color: var(--white); font-weight: 700; font-size: 20px; text-align: center; line-height: 1; }
  .origin__stars { display: block; font-size: 10px; letter-spacing: 3px; margin-top: 2px; }

  .sae-mark { left: 327px; top: 320px; color: var(--white); font-weight: 900; font-size: 38px; line-height: 1; }
  .vertical { position: absolute; writing-mode: vertical-rl; color: var(--white); font-weight: 900; white-space: nowrap; }
  .viscosity { left: 322px; top: 357px; font-size: 94px; line-height: .75; letter-spacing: -1px; }
  .spec { left: 290px; top: 532px; font-size: 30px; line-height: .9; }
  .product-line { left: 413px; top: 329px; font-size: 36px; line-height: .9; letter-spacing: 1px; }

  /* Back */
  .back-name { left: 23px; top: 37px; font-size: 42px; }
  .back-sub { left: 101px; top: 76px; font-size: 12px; }
  .back-grade-title { left: 50px; top: 95px; width: 122px; text-align: center; font-size: 11px; -webkit-text-stroke: 2px #111; }
  .back-sae { left: 50px; top: 112px; writing-mode: vertical-rl; transform: rotate(180deg); font-size: 11px; font-weight: 900; color: var(--brand-blue); line-height: 1; }
  .back-vis { left: 64px; top: 104px; font-size: 42px; font-weight: 900; color: var(--brand-blue); line-height: 1; }
  .back-spec { left: 127px; top: 143px; font-size: 10px; font-weight: 900; color: var(--brand-blue); line-height: 1; }
  .back-tagline { left: 196px; top: 116px; width: 140px; font-size: 13px; }
  .back-seal { left: 338px; top: 40px; width: 102px; height: 102px; }

  .copy {
    position: absolute; left: 17px; top: 162px; width: 436px;
    font-size: 15px; line-height: 20.4px; font-weight: 300; text-align: justify; color: var(--ink);
  }
  .copy strong { font-weight: 700; }
  .accent-red { color: var(--brand-red); font-weight: 700; }
  .accent-blue { color: var(--brand-blue); font-weight: 700; }
  .benefits { list-style: none; }
  .benefits li { position: relative; padding-left: 44px; color: var(--brand-blue); font-weight: 700; font-size: 15.5px; }
  .benefits li::before { content: "•"; position: absolute; left: 0; }

  .fine {
    position: absolute; left: 17px; width: 325px; font-size: 12px; line-height: 16.4px;
    text-align: justify; color: var(--ink); font-weight: 400;
  }
  .fine--quality { top: 462px; }
  .fine--warning { top: 544px; }
  .fine--recycle { top: 643px; text-align: left; }
  .fine__head { display: block; color: var(--brand-red); font-weight: 700; font-size: 12.5px; }

  .service-mark {
    position: absolute; left: 260px; top: 659px; width: 78px; height: 78px; border-radius: 50%;
    background: var(--white); border: 2px solid #333;
  }
  .service-mark::after { content: ""; position: absolute; inset: 14px; border-radius: 50%; border: 1.5px solid #333; }

  .sus { left: 363px; top: 455px; font-size: 24px; font-weight: 700; color: var(--white); line-height: 1; }
  .code-panel { position: absolute; left: 353px; top: 485px; width: 99px; height: 175px; background: var(--white); }
  .flag { position: absolute; left: 353px; top: 665px; width: 99px; height: 52px; }
  .made-in { position: absolute; left: 353px; top: 718px; width: 99px; background: var(--white); text-align: center; font-size: 13px; font-weight: 700; letter-spacing: 1px; line-height: 17px; }
</style>
</head>
<body>

<section class="label label--front" aria-label="Front label">
  <svg class="label__shapes" viewBox="0 0 469 759" aria-hidden="true">
    <path fill="var(--brand-red)" d="M92,0 C180,60 330,82 469,124 L469,60 C430,55 330,30 256,0 Z"/>
    <path fill="var(--brand-blue)" d="M256,0 C330,30 430,55 469,60 L469,0 Z"/>
    <path fill="var(--brand-red)" d="M290,285 C235,365 205,450 202,540 C200,620 192,700 186,759 L469,759 L469,690 Z"/>
    <path fill="var(--brand-blue)" d="M469,140 C410,170 340,250 302,335 C262,420 212,470 222,535 C240,625 390,690 469,712 Z"/>
  </svg>

  <div class="abs brand-name front-name">CORVANA</div>
  <div class="abs brand-sub front-sub">LUBRICANTS</div>

  <div class="abs outlined front-grade-title">SYNTHETIC BLEND</div>
  <div class="abs tagline front-tagline">
    <span class="tagline__top">MOST ADVANCED</span>
    <span class="tagline__bottom">PERFORMANCE</span>
  </div>
  <p class="abs promise">MAXIMUM PROTECTION<br>FOR MORE MILES</p>

  <div class="seal front-seal" role="img" aria-label="Certification seal"></div>

  <div class="abs sae-mark">SAE</div>
  <div class="vertical viscosity">5W-30</div>
  <div class="vertical spec">ALSC SN</div>
  <div class="vertical product-line">SYNTHETIC BLEND</div>

  <div class="abs volume">32oz 1946mU</div>
  <div class="abs origin">Made In USA<span class="origin__stars">★★★</span></div>
</section>

<section class="label label--back" aria-label="Back label">
  <svg class="label__shapes" viewBox="0 0 469 759" aria-hidden="true">
    <path fill="var(--brand-red)" d="M150,0 C250,30 380,55 469,92 L469,48 C400,35 330,20 272,0 Z"/>
    <path fill="var(--brand-blue)" d="M272,0 C330,20 400,35 469,48 L469,0 Z"/>
  </svg>

  <div class="abs brand-name back-name">CORVANA</div>
  <div class="abs brand-sub back-sub">LUBRICANTS</div>

  <div class="abs outlined back-grade-title">SYNTHETIC BLEND</div>
  <div class="abs back-sae">SAE</div>
  <div class="abs back-vis">5W-30</div>
  <div class="abs back-spec">ALSC SN</div>

  <div class="abs tagline back-tagline">
    <span class="tagline__top">MOST ADVANCED</span>
    <span class="tagline__bottom">PERFORMANCE</span>
  </div>

  <div class="seal back-seal" role="img" aria-label="Certification seal"></div>

  <div class="copy">
    <p><span class="accent-red">CORVANA MOTOR OIL</span> <span class="accent-blue">5W30 and SAE</span> <strong>Synthetic Blend Motor Oil provides the ultimate performance and protection, especially under severe driving conditions.</strong> It utilized newly developed additive technology to achieve among the lowest retes of wear ever for motor oils, well exceeding the most stringent North American specifications for wear control, cleanliness and sludge, oxidation control, and emission system and seal compatibility, while meeting the standards for fuel economy.</p>
    <p><span class="accent-blue">Licensed IMLC GF-5 and ALSC SN</span> “Resource Conserving” by the American Lubricant Standards Council (ALSC) as all previous service classification. It is compatible with all conventional and synthetic oils.</p>
    <ul class="benefits">
      <li>Provides Protections That Conventional Oils Can’t</li>
      <li>Won’t Break Down Under Extreme Temperature</li>
      <li>Superior Protection For Extended Service Intervals.</li>
    </ul>
  </div>

  <p class="fine fine--quality"><span class="accent-red">CORVANA MOTOR OIL</span> is manufactured to stringent standards. Every batch is tested, from raw materials to finished product, to insure you’re getting the Best Protection and Highest Performance from every quart.</p>

  <p class="fine fine--warning"><span class="fine__head">WARNING! AVOID SKIN CONTACT WITH USED MOTOR OIL!</span>Used moter oils have caused skin cancer in laboratory, animals when repeatedly applied and left in place between applications, In case of skin contact promptly wash thoroughly with soap and water, Oil soild clothing should be cleand before reuse</p>

  <p class="fine fine--recycle">DON’T POLLUTE! Conserve resources<br>Take used oil to collection center.</p>

  <div class="service-mark" role="img" aria-label="Service symbol"></div>

  <div class="abs sus">SUS 350</div>
  <div class="code-panel"></div>
  <svg class="flag" viewBox="0 0 99 52" preserveAspectRatio="none" role="img" aria-label="United States flag">
    <rect width="99" height="52" fill="var(--white)"/>
    <g fill="#c8102e">
      <rect y="0" width="99" height="4"/><rect y="8" width="99" height="4"/>
      <rect y="16" width="99" height="4"/><rect y="24" width="99" height="4"/>
      <rect y="32" width="99" height="4"/><rect y="40" width="99" height="4"/>
      <rect y="48" width="99" height="4"/>
    </g>
    <rect width="42" height="28" fill="#1f3a7a"/>
  </svg>
  <div class="made-in">MADE IN USA</div>
</section>

</body>
</html>
```